Dietitian needs awesome business card

I need a contemporary design that's eye catching but professional.
My card is to given to doctors, specialists and patients alike.
I manage patients with chronic diseases
I have uploaded my logo and current business card, I would also like the other Certified Clinical Nutritionist logo incorporated into the design

Target Market(s)

Doctors, specialists and patients

Industry/Entity Type

Healthcare

Contact Information for Business Card

www.brightfieldnutrition.com.au
Ph: 0427 561 903
Fax: 6457 2183
email: marcus.k.diet@fernmail.com
Space on the back of the card with: Appointment date, Appointment time and appointment location

Font styles to use
Serif

Colors
fbee3e
876aae
ffc214

Requirements
Must have
• My Logo
• Certified Clinical Nutritionist Logo
• My 4 locations - Pinebrook Medical Centre, North Corrin Health, Hollis Medical, Ashcombe Doctors Surgery
Nice to have
• I like the colours in my current business card

```html
<!DOCTYPE html>
<html lang="en">
<head>
<meta charset="utf-8">
<title>Brightfield Nutrition &amp; Dietetics – Business Card</title>
<link href="https://fonts.googleapis.com/css2?family=Philosopher:wght@400;700&family=Open+Sans:wght@400&display=swap" rel="stylesheet">
<style>
  :root {
    --backdrop: #e9e9e9;
    --card: #ffffff;
    --navy: #1d3c8f;
    --green: #8dc63f;
    --ink: #4a4a4a;
    --divider: #c9c9c9;
    --badge: #f47a20;
    --checkbox: #2a4a9a;
  }
  * { box-sizing: border-box; margin: 0; padding: 0; }
  html, body {
    width: 1105px; height: 1200px; overflow: hidden;
    background: var(--backdrop);
  }
  .card {
    position: absolute; left: 182px; width: 746px; height: 424px;
    background: var(--card); overflow: hidden;
    box-shadow: 0 6px 14px rgba(0,0,0,0.18);
  }
  .card--front { top: 120px; }
  .card--back { top: 636px; }

  /* Front */
  .brand {
    position: absolute; left: 48px; top: 186px;
    display: flex; align-items: center; gap: 12px;
  }
  .brand__dot { width: 22px; height: 22px; border-radius: 50%; background: var(--navy); }
  .brand__name {
    font-family: 'Philosopher', serif; font-weight: 400; font-size: 27px;
    color: var(--navy); line-height: 1.15; width: 250px;
  }
  .divider {
    position: absolute; left: 353px; top: 115px; width: 1px; height: 193px;
    background: var(--divider);
  }
  .person { position: absolute; left: 382px; top: 114px; }
  .person__name {
    font-family: 'Philosopher', serif; font-size: 28px; color: var(--navy);
  }
  .person__role {
    font-family: 'Philosopher', serif; font-size: 19px; color: var(--green);
    margin-top: 2px;
  }
  .contacts { list-style: none; position: absolute; left: 382px; top: 190px; }
  .contacts__item {
    display: flex; align-items: center; gap: 10px; height: 29px;
    font-family: 'Philosopher', serif; font-size: 20px; color: var(--ink);
  }
  .contacts__icon { width: 18px; height: 18px; fill: var(--navy); flex: none; }

  /* Back */
  .brand-watermark {
    position: absolute; left: -20px; top: 80px; width: 370px; height: 370px;
    border-radius: 50%;
    background: radial-gradient(circle at 40% 40%, rgba(190,205,235,0.35), rgba(210,230,180,0.25) 70%, rgba(255,255,255,0) 72%);
  }
  .credential-badge {
    position: absolute; left: 382px; top: 48px; width: 178px; height: 83px;
    background: var(--badge); border-radius: 2px;
  }
  .appointment {
    position: absolute; left: 382px; font-family: 'Open Sans', sans-serif;
    font-size: 20px; color: var(--navy);
  }
  .appointment--date { top: 176px; }
  .appointment--time { top: 222px; }
  .appointment__fill { color: var(--navy); letter-spacing: 1px; font-size: 16px; }
  .appointment__suffix { font-size: 15px; margin-left: 6px; }
  .locations { list-style: none; position: absolute; left: 382px; top: 282px; }
  .locations__item {
    display: flex; align-items: center; gap: 14px; height: 27px;
    font-family: 'Open Sans', sans-serif; font-size: 19px; color: var(--ink);
  }
  .locations__box {
    width: 16px; height: 16px; border: 1.5px solid var(--checkbox); flex: none;
  }
</style>
</head>
<body>

<section class="card card--front" aria-label="Card front">
  <div class="brand">
    <span class="brand__dot"></span>
    <span class="brand__name">Brightfield Nutrition &amp; Dietetics</span>
  </div>
  <div class="divider"></div>
  <div class="person">
    <h1 class="person__name">Marcus Kellaway</h1>
    <p class="person__role">Nutritionist &amp; Chef</p>
  </div>
  <ul class="contacts">
    <li class="contacts__item">
      <svg class="contacts__icon" viewBox="0 0 24 24" aria-hidden="true"><path d="M6.6 10.8c1.4 2.8 3.8 5.1 6.6 6.6l2.2-2.2c.3-.3.7-.4 1-.2 1.1.4 2.3.6 3.6.6.6 0 1 .4 1 1V20c0 .6-.4 1-1 1C10.6 21 3 13.4 3 4c0-.6.4-1 1-1h3.5c.6 0 1 .4 1 1 0 1.3.2 2.5.6 3.6.1.3 0 .7-.2 1z"/></svg>
      0427 561 903
    </li>
    <li class="contacts__item">
      <svg class="contacts__icon" viewBox="0 0 24 24" aria-hidden="true"><path d="M6 2h10l2 2v5H6z M3 10h18v9H3z M7 17h10v5H7z"/></svg>
      6457 2183
    </li>
    <li class="contacts__item">
      <svg class="contacts__icon" viewBox="0 0 24 24" aria-hidden="true"><path d="M2 5h20v14H2z M3 6l9 7 9-7" stroke="#fff" stroke-width="1.5"/></svg>
      marcus.k.diet@fernmail.com
    </li>
    <li class="contacts__item">
      <svg class="contacts__icon" viewBox="0 0 24 24" aria-hidden="true"><circle cx="12" cy="12" r="10"/><path d="M2 12h20M12 2c3 3 3 17 0 20M12 2c-3 3-3 17 0 20" stroke="#fff" stroke-width="1.3" fill="none"/></svg>
      brightfieldnutrition.com.au
    </li>
  </ul>
</section>

<section class="card card--back" aria-label="Card back">
  <div class="brand-watermark" role="img" aria-label="Faint brand decoration"></div>
  <div class="credential-badge" role="img" aria-label="Certified Clinical Nutritionist badge"></div>
  <p class="appointment appointment--date">Date : <span class="appointment__fill">......................................</span></p>
  <p class="appointment appointment--time">Time : <span class="appointment__fill">..........................</span><span class="appointment__suffix">AM/PM</span></p>
  <ul class="locations">
    <li class="locations__item"><span class="locations__box"></span>Pinebrook Medical Centre</li>
    <li class="locations__item"><span class="locations__box"></span>North Corrin Health</li>
    <li class="locations__item"><span class="locations__box"></span>Hollis Medical</li>
    <li class="locations__item"><span class="locations__box"></span>Ashcombe Doctors Surgery</li>
  </ul>
</section>

</body>
</html>
```